Taro Reserve website (www.taroreserve.com)

My company develops booking software, Taro Reserve, for the hourly booking of resources such as classes in a school or customer booking involving rooms in a spa. These bookings also involve the customers, staff, rooms and a lesson or treatment.

The main difference between this software and general calendar software such as Plonkit calendar is that this Taro Reserve allows resources such as people and rooms to be associated with the bookings. This is important for example in the case of a Spa to make sure the rooms are booked appropriately and to see the free times for the rooms. For a golf practice range the players much be booked to the tee spots where they practice golf.

I have tried to design the website myself, as a computer programmer- I am a bit "square" and not a designer, my first attempt is http://www.taroreserve.com/, my second attempt is at http://www.lumex-works.com/taroreservewebsite/
I am not happy with my designs as compared to the professional designs I see people can come up with here. The software must have the image of a professional software product in order to inspire the confidence of customers.

Am looking for a design which will be the most likely to give the customer the following feeling:
* Confident the product can do the job.
* Feel easy to want to try it, at least for the free trial.
* Its a professional software product and also a web based product, the user can login from the web.

Look at other booking software websites for ideas, here is a list of links to similar booking products. These products all have different features but are mostly for resource booking.
http://lumex-works.com/taroreservewebsite/?page=compare
Updates

Hello all,

Thankyou for the designs so far, to save peoples time, I will try to eliminate the bottom 50% of designs now.

To be honest, most of the designs are of a good or high quality, I think its very tough on you as graphic and web designers. Only a minor few are of low quality.

If your design is discarded - I would say its unlikely that you are going to be able to produce a design that will beat the competition. 
You probably already know, you could try to re-sell your design later for other projects or as a template on one of those template websites. Some of these discarded designs are quite worthwhile designs.

Best regards, Gordon

Target Market(s)

Spa, Gym, School, Golf, any organization who manages bookings of their customers

Industry/Entity Type

Software

Requirements
Must have
• Home page and inner page, any other pages up to you.

Make a logo or use the image of the girl that I already have on the second design.

Menu(s) for navigation.

A language switcher for 3 languages, English, Chinese Traditional and Chinese Simplified. (Western, Hong Kong and Chinese mainland market are important).

Space for a video introduction, it could be small and when the user clicks on it then it gets bigger then it won't take up too much space. Up to you.

A space for the user to login and register a new account.

Screenshots.

I don't have any strong preferences, use your own ideas, if you look at all the other products you can get the basic idea from them.

The total goal is to make a website which is going to lead to sales of the software product.

```html
<!DOCTYPE html>
<html lang="en">
<head>
<meta charset="utf-8">
<title>Taro Reserve – Create a New Booking</title>
<link href="https://fonts.googleapis.com/css2?family=Mulish:wght@400;600;700;800&display=swap" rel="stylesheet">
<style>
  :root {
    --topbar: #3a3c3d;
    --teal-dark: #1f4c52;
    --teal-mid: #2f646a;
    --teal-text: #4f9aa0;
    --nav-bg: #2d3031;
    --nav-item: #3b3e40;
    --nav-text: #f2f2f2;
    --accent-green: #8fce3c;
    --page-bg: #f0f3ea;
    --book-cover: #2b2c2d;
    --paper-left: #e3e5e6;
    --paper-right: #e9ebec;
    --rule: #c4c7c9;
    --ink: #4a4c4e;
    --ink-soft: #7b7e80;
    --ink-faint: #9a9d9f;
    --field-border: #b9d6da;
    --field-bg: #ffffff;
    --footer-bg: #2f3233;
    --footer-text: #d8d9d9;
    --plus-green: #7dbb4c;
    --binding-dark: #1c1d1e;
    --binding-light: #6c6f71;
  }
  * { box-sizing: border-box; margin: 0; padding: 0; }
  html, body { width: 1200px; height: 900px; overflow: hidden; }
  body {
    position: relative;
    background: var(--page-bg);
    font-family: "Mulish", Arial, sans-serif;
    color: var(--ink);
  }

  /* Header */
  .topbar { position: absolute; left: 0; top: 0; width: 1200px; height: 28px; background: var(--topbar); }
  .masthead {
    position: absolute; left: 0; top: 28px; width: 1200px; height: 113px;
    background: linear-gradient(90deg, var(--teal-dark) 0%, var(--teal-mid) 45%, var(--teal-dark) 100%);
  }
  .brand {
    position: absolute; left: 80px; top: 50px; width: 172px; height: 91px;
    background: #141414; display: flex; align-items: center; justify-content: center;
    color: #ffffff; font-weight: 700; font-size: 18px; line-height: 1.15; text-align: center;
  }
  .services {
    position: absolute; left: 296px; top: 79px; display: flex; align-items: center; gap: 22px;
    font-weight: 800; font-size: 17.5px; letter-spacing: 0.3px; color: var(--teal-text); text-transform: uppercase;
  }
  .services .dot { width: 7px; height: 7px; border-radius: 50%; background: var(--teal-text); }

  .navbar { position: absolute; left: 0; top: 141px; width: 1200px; height: 43px; background: var(--nav-bg); }
  .nav-list { position: absolute; left: 136px; top: 0; display: flex; gap: 2px; list-style: none; }
  .nav-list li {
    height: 43px; background: var(--nav-item); color: var(--nav-text);
    font-weight: 700; font-size: 15px; display: flex; align-items: center; justify-content: center;
  }
  .nav-list li.current { border-bottom: 3px solid var(--accent-green); }
  .search {
    position: absolute; left: 1028px; top: 144px; width: 162px; height: 36px; border-radius: 18px;
    background: #1f2a2e; color: #8d9aa0; font-size: 14px; display: flex; align-items: center; padding-left: 16px; gap: 8px;
  }

  /* Booking book */
  .book { position: absolute; left: 77px; top: 219px; width: 1026px; height: 592px; background: var(--book-cover); border-radius: 16px; }
  .page-stack { position: absolute; left: 1050px; top: 244px; width: 34px; height: 540px; background: #cfd2d4; border-radius: 0 4px 4px 0; }
  .page-left { position: absolute; left: 96px; top: 238px; width: 290px; height: 554px; background: var(--paper-left); }
  .spine { position: absolute; left: 386px; top: 238px; width: 13px; height: 554px; background: #161616; }
  .page-right { position: absolute; left: 399px; top: 238px; width: 668px; height: 554px; background: var(--paper-right); }
  .binding {
    position: absolute; left: 370px; width: 44px; border-radius: 6px;
    background: linear-gradient(90deg, var(--binding-dark) 0%, var(--binding-light) 50%, var(--binding-dark) 100%);
  }

  .profile-welcome { position: absolute; left: 96px; top: 268px; width: 268px; text-align: center; font-size: 17px; font-weight: 700; color: var(--ink-faint); }
  .rule-left { position: absolute; left: 123px; width: 222px; height: 1px; background: var(--rule); }
  .profile-name { position: absolute; left: 96px; top: 330px; width: 268px; text-align: center; font-size: 17px; font-weight: 700; color: #3e4042; }
  .contact { position: absolute; left: 141px; font-size: 13px; color: var(--ink); line-height: 1.35; }
  .contact dt { font-weight: 800; }
  .btn {
    position: absolute; height: 30px; border-radius: 4px; border: 1px solid #b7babc;
    background: linear-gradient(#f4f5f5, #d4d6d7); font-size: 14px; font-weight: 600; color: var(--ink-soft);
    display: flex; align-items: center; justify-content: center;
  }
  .news-head { position: absolute; left: 135px; top: 577px; font-size: 15px; font-weight: 700; color: #3e4042; }
  .news-item { position: absolute; left: 135px; font-size: 13px; color: var(--ink); line-height: 1.4; }
  .news-item time { display: block; font-size: 11.5px; color: var(--ink-soft); }

  .form-title { position: absolute; left: 446px; top: 258px; font-size: 16px; font-weight: 700; color: #505254; display: flex; align-items: center; gap: 9px; }
  .rule-right { position: absolute; left: 446px; width: 552px; height: 1px; background: var(--rule); }
  .steps { position: absolute; left: 438px; top: 313px; }
  .section-title { position: absolute; left: 448px; top: 378px; font-size: 15.5px; font-weight: 700; color: #505254; }
  .field-label { position: absolute; left: 430px; width: 108px; text-align: right; font-size: 15px; font-weight: 700; color: #5a5c5e; }
  .field {
    position: absolute; left: 557px; width: 362px; height: 35px; background: var(--field-bg);
    border: 1px solid var(--field-border); border-radius: 3px; font-size: 14px; color: var(--ink-soft);
    padding: 9px 11px;
  }
  .field-select .arrow { position: absolute; right: 0; top: 0; width: 42px; height: 33px; border-left: 1px solid var(--field-border); display: flex; align-items: center; justify-content: center; }

  /* Footer */
  .footer { position: absolute; left: 0; top: 848px; width: 1200px; height: 52px; background: var(--footer-bg); color: var(--footer-text); font-size: 11px; font-weight: 700; }
  .footer-social { position: absolute; left: 22px; top: 18px; display: flex; align-items: center; gap: 10px; }
  .footer-social .square { width: 18px; height: 18px; background: #4a6aa8; border-radius: 2px; }
  .footer-links { position: absolute; left: 222px; top: 21px; display: flex; gap: 37px; list-style: none; }
  .footer-copy { position: absolute; right: 22px; top: 21px; color: #8c8f90; font-weight: 600; }
</style>
</head>
<body>

<header>
  <div class="topbar"></div>
  <div class="masthead"></div>
  <div class="brand">Serene Spa<br>Advisors</div>
  <div class="services">
    <span>Spa Consulting</span><span class="dot"></span>
    <span>Spa Planning</span><span class="dot"></span>
    <span>Spa Operations Setup</span><span class="dot"></span>
    <span>Spa Treatments</span>
  </div>
  <nav class="navbar">
    <ul class="nav-list">
      <li style="width:99px">Home</li>
      <li class="current" style="width:110px">Bookings</li>
      <li style="width:99px">Free Trial</li>
      <li style="width:138px">Documentation</li>
      <li style="width:107px">Compare</li>
      <li style="width:105px">Feedback</li>
      <li style="width:103px">Purchase</li>
      <li style="width:108px">Contact</li>
    </ul>
  </nav>
  <div class="search">
    <svg width="14" height="14" viewBox="0 0 14 14"><circle cx="5.5" cy="5.5" r="4.3" fill="none" stroke="#8d9aa0" stroke-width="1.8"/><line x1="8.7" y1="8.7" x2="13" y2="13" stroke="#8d9aa0" stroke-width="2"/></svg>
    Search
  </div>
</header>

<main>
  <div class="book"></div>
  <div class="page-stack"></div>
  <section class="page-left"></section>
  <div class="spine"></div>
  <section class="page-right"></section>

  <div class="binding" style="top:289px;height:135px" role="img" aria-label="Upper set of metal binder rings joining the two pages"></div>
  <div class="binding" style="top:600px;height:135px" role="img" aria-label="Lower set of metal binder rings joining the two pages"></div>

  <h2 class="profile-welcome">Welcome</h2>
  <div class="rule-left" style="top:310px"></div>
  <h3 class="profile-name">Serene Spa Advisors</h3>
  <div class="rule-left" style="top:366px"></div>
  <dl class="contact" style="top:390px"><dt>Website:</dt><dd>www.serenespaadvisors.com</dd></dl>
  <dl class="contact" style="top:440px"><dt>Email:</dt><dd>hello@serenespaadvisors.com</dd></dl>
  <dl class="contact" style="top:487px"><dt>Phone:</dt><dd>+27 555 0192</dd></dl>
  <div class="btn" style="left:258px;top:498px;width:92px">Sign Out</div>
  <div class="rule-left" style="top:554px"></div>
  <h3 class="news-head">Latest News</h3>
  <p class="news-item" style="top:609px">News title goes here<time>31 October 2011</time></p>
  <p class="news-item" style="top:662px">News title goes here<time>29 October 2011</time></p>
  <p class="news-item" style="top:715px">News title goes here<time>8 October, 2011</time></p>

  <h2 class="form-title">
    <svg width="17" height="17" viewBox="0 0 17 17"><path d="M6 0h5v6h6v5h-6v6H6v-6H0V6h6z" fill="var(--plus-green)"/></svg>
    Create a New Booking
  </h2>
  <div class="rule-right" style="top:293px"></div>

  <svg class="steps" width="572" height="36" viewBox="0 0 572 36" font-family="Mulish, Arial, sans-serif" font-size="14">
    <rect x="0.5" y="0.5" width="571" height="34" rx="2" fill="#f3f4f4" stroke="#c9cccd"/>
    <path d="M0.5 0.5H130L145 17.5L130 34.5H0.5Z" fill="#ffffff" stroke="#c9cccd"/>
    <path d="M272 0.5L287 17.5L272 34.5M415 0.5L430 17.5L415 34.5" fill="none" stroke="#c9cccd"/>
    <text x="31" y="22" fill="#3e4042" font-weight="700">1. Details</text>
    <text x="164" y="22" fill="#8a8d8f" font-weight="600">2. Date &amp; Time</text>
    <text x="318" y="22" fill="#8a8d8f" font-weight="600">3. Schedule</text>
    <text x="469" y="22" fill="#8a8d8f" font-weight="600">4. Confirm</text>
  </svg>

  <h3 class="section-title">Customer Details</h3>
  <div class="rule-right" style="top:408px"></div>

  <label class="field-label" style="top:443px">Name:</label>
  <div class="field" style="top:435px">Name</div>
  <label class="field-label" style="top:490px">Phone:</label>
  <div class="field" style="top:482px">Phone</div>
  <label class="field-label" style="top:537px">Email:</label>
  <div class="field" style="top:529px">Email Address</div>
  <label class="field-label" style="top:584px">Group:</label>
  <div class="field field-select" style="top:576px">Amont of People Attending
    <span class="arrow"><svg width="14" height="8" viewBox="0 0 14 8"><path d="M0 0h14L7 8z" fill="#7e9aa0"/></svg></span>
  </div>
  <label class="field-label" style="top:631px">Notes:</label>
  <div class="field" style="top:623px;height:100px">Special Requirements &nbsp;/&nbsp; Medical Conditions</div>

  <div class="rule-right" style="top:760px;width:472px"></div>
  <div class="btn" style="left:951px;top:746px;width:90px;height:32px">next...</div>
</main>

<footer class="footer">
  <div class="footer-social"><span class="square"></span>Join Us on Chatterly</div>
  <ul class="footer-links">
    <li>About</li><li>Events</li><li>Press</li><li>Jobs</li><li>Staff</li><li>Resources</li>
    <li>Privacy</li><li>T&amp;Cs</li><li>Feedback</li><li>Customer Service</li><li>Contact</li>
  </ul>
  <div class="footer-copy">© 2011 Taro Reserve</div>
</footer>

</body>
</html>
```